Tusk Hollow Lodge website (design only)

Tusk Hollow Lodge (http://www.tuskhollowlodge-mw.example) is a private Safari lodge located in Kaliwa Valley.
We would like a modern, professional website designed that does not subscribe to the cliched view of a Safari in Africa, but still maintain a wildlife/safari atmosphere.

The aim of our website is to entice people & drive them to the booking form.

Here are some examples of websites that we like. Although we would like our site to be a bit more in line with modern web design trends.

http://www.marulaplains.example/
http://www.kovunde.example/
http://www.tembalorecamp.example/

Requirements
Must have
• Here is a list of the pages required. Most of them will follow a standard content layout. I.e. heading, body and images.

If you take a look at the website, you will get an idea of hoe many page types there are +- 5

http://www.tuskhollowlodge-mw.example/index.htm

About Tusk Hollow
Lirundu Country Club
Rooms
Conferences
Cuisine
Facilities
Your Safari
Activities
Rates & Special Offers
Booking form
Latest Developments
How To Get There
Gallery
Contact Us
Blog / Newsfeed

```html
<!DOCTYPE html>
<html lang="en">
<head>
<meta charset="utf-8">
<title>Tusk Hollow Lodge</title>
<link href="https://fonts.googleapis.com/css2?family=Open+Sans:wght@400;600;700&display=swap" rel="stylesheet">
<style>
:root{
  --bg:#0a1b2a;
  --panel:#10293d;
  --panel-edge:#1b3b55;
  --nav-top:#2a6da0;
  --nav-bottom:#174a74;
  --accent:#3aa9dc;
  --text:#c9d6e0;
  --muted:#8fa4b5;
  --white:#ffffff;
}
*{box-sizing:border-box;margin:0;padding:0}
html,body{width:837px;height:1200px;overflow:hidden}
body{background:var(--bg);font-family:"Open Sans",Arial,sans-serif;color:var(--text);position:relative}
a{color:inherit;text-decoration:none}

.site-header{position:absolute;left:14px;right:14px;top:0;height:50px}
.brand{position:absolute;left:4px;top:12px;font-weight:700;font-size:19px;color:var(--white);letter-spacing:.5px;text-transform:uppercase}
.search{position:absolute;right:0;top:7px;width:140px;height:17px;background:#e9eef2;border:1px solid #9fb2c2;font-size:9px;color:#667;padding:2px 6px}
.search svg{position:absolute;right:4px;top:3px}
.top-links{position:absolute;right:0;top:32px;display:flex;gap:16px;font-size:10px;color:var(--white)}

.main-nav{position:absolute;left:14px;right:14px;top:54px;height:22px;background:linear-gradient(var(--nav-top),var(--nav-bottom));display:flex;align-items:center;justify-content:space-between;padding:0 10px;font-size:10px;color:var(--white)}

.hero{position:absolute;left:14px;right:14px;top:80px;height:330px;background:linear-gradient(180deg,#5d8f66 0%,#3f6b3c 40%,#7a6a4a 62%,#5c8a45 80%,#4a7436 100%)}
.slider-dots{position:absolute;left:14px;bottom:12px;display:flex;gap:4px}
.slider-dots span{width:14px;height:12px;background:rgba(255,255,255,.85);color:#123;font-size:8px;text-align:center;line-height:12px}
.slider-dots span.on{background:var(--accent);color:#fff}

.features{position:absolute;left:14px;right:14px;top:422px;display:grid;grid-template-columns:repeat(4,1fr);gap:14px}
.feature .thumb{height:100px}
.feature h3{font-weight:400;font-size:16px;color:var(--accent);margin:8px 0 3px}
.feature p{font-size:9.5px;line-height:13px;color:var(--text);height:40px}
.more{display:block;margin-top:8px;font-size:9.5px;color:var(--muted)}

.panel{position:absolute;background:var(--panel);border:1px solid var(--panel-edge)}
.panel h2{font-weight:400;font-size:16px;color:var(--accent);padding:10px 12px 6px}
.directions{left:14px;top:622px;width:396px;height:216px}
.directions .info{position:absolute;left:12px;top:40px;width:210px;font-size:9.5px;line-height:15px;text-transform:uppercase}
.directions .info p{margin-bottom:10px}
.map{position:absolute;right:12px;top:40px;width:150px;height:112px;background:linear-gradient(135deg,#dfe6c8,#b9cf9d 55%,#e7dcb6)}
.updates{left:424px;top:622px;width:399px;height:216px}
.updates h4{font-size:9.5px;font-weight:600;color:var(--white);padding:4px 12px 6px;letter-spacing:.5px}
.updates p{font-size:9.5px;line-height:14px;padding:0 12px}

.welcome{left:14px;top:852px;width:809px;height:182px}
.welcome h2{font-size:18px;padding:14px 14px 10px}
.welcome p{font-size:10.5px;line-height:17px;padding:6px 14px 0}

.site-footer{position:absolute;left:14px;right:14px;top:1046px;height:140px}
.footer-links{position:absolute;left:10px;top:8px;display:flex;gap:60px}
.footer-links ul{list-style:none;font-size:9.5px;color:var(--white)}
.footer-links li{line-height:17px;padding-left:12px;position:relative}
.footer-links li::before{content:"";position:absolute;left:0;top:6px;width:4px;height:4px;background:var(--white)}
.follow{position:absolute;right:0;top:4px;display:flex;align-items:center;gap:5px}
.follow span{font-size:13px;color:var(--accent);margin-right:6px}
.follow i{display:block;width:14px;height:14px;border-radius:50%;background:var(--accent)}
.address{position:absolute;right:0;top:50px;width:320px;text-align:right;font-size:9px;line-height:13px;color:var(--text);white-space:nowrap}
.copyright{position:absolute;right:0;top:92px;font-size:8.5px;color:var(--muted)}
</style>
</head>
<body>

<header class="site-header">
  <div class="brand">Tusk Hollow Lodge</div>
  <div class="search">search
    <svg width="9" height="9" viewBox="0 0 9 9"><circle cx="3.6" cy="3.6" r="2.6" fill="none" stroke="#567" stroke-width="1.2"/><line x1="5.6" y1="5.6" x2="8.5" y2="8.5" stroke="#567" stroke-width="1.3"/></svg>
  </div>
  <nav class="top-links"><a>Home</a><a>About Tusk Hollow</a><a>Gallery</a><a>Our Blog</a></nav>
</header>

<nav class="main-nav">
  <a>Rooms</a><a>Conferences</a><a>Cuisine</a><a>Facilities</a><a>Your Safari</a><a>Activities</a><a>Rates &amp; Special Offers</a><a>Booking inquiries</a><a>Latest Developments</a><a>How To Get There</a>
</nav>

<section class="hero" role="img" aria-label="Photo of the lodge building with red roofs among tall trees and a green lawn">
  <div class="slider-dots"><span class="on">1</span><span>2</span><span>3</span><span>4</span></div>
</section>

<section class="features">
  <article class="feature">
    <div class="thumb" role="img" aria-label="Photo of zebra grazing in the game park" style="background:linear-gradient(160deg,#6f8c4a,#4e6a33 60%,#8c8a63)"></div>
    <h3>facilities</h3>
    <p>Game park with wildlife including Giraffe, Zebra, Sable, Eland, Impala and the Lirundu Golf Course.</p>
    <a class="more">know more »</a>
  </article>
  <article class="feature">
    <div class="thumb" role="img" aria-label="Photo of an antelope in golden grass" style="background:linear-gradient(160deg,#c8822f,#a1611f 55%,#6d4a22)"></div>
    <h3>your safari</h3>
    <p>The animals in the game sanctuary are best seen on a guided game drive at dawn or dusk.</p>
    <a class="more">know more »</a>
  </article>
  <article class="feature">
    <div class="thumb" role="img" aria-label="Photo of the lodge grounds and gardens" style="background:linear-gradient(170deg,#7fa4b8,#5b8a57 50%,#8d5a3c)"></div>
    <h3>activities</h3>
    <p>Bush walks, game drives, bird watching, fishing, golf and a swimming pool for all guests.</p>
    <a class="more">know more »</a>
  </article>
  <article class="feature">
    <div class="thumb" role="img" aria-label="Photo of a lodge chalet with a red roof" style="background:linear-gradient(170deg,#8fb1c4,#9a5a3e 50%,#5d7f44)"></div>
    <h3>rates and special offers</h3>
    <p>Rates per person sharing include bed and breakfast, with seasonal offers on longer stays.</p>
    <a class="more">know more »</a>
  </article>
</section>

<section class="panel directions">
  <h2>how to get there</h2>
  <div class="info">
    <p>Tusk Hollow Lodge is situated at Nsonga estate.</p>
    <p>Directions on Kaliwa road</p>
    <p>Look out for the lodge sign</p>
    <p>Only 12 km from Nkhombe and 20 km from Lusaya</p>
  </div>
  <div class="map" role="img" aria-label="Road map showing the route to the lodge"></div>
</section>

<section class="panel updates">
  <h2>tusk hollow updates</h2>
  <h4>PROJECT DEVELOPMENT</h4>
  <p>The lodge was opened in February 2011 and work continues on new rooms. Construction of the 18 hole Lirundu golf course was completed, with the clubhouse and pro shop to follow. A further wing of six chalets with views over the water hole is being built, and a new spa is planned for the next season.</p>
</section>

<section class="panel welcome">
  <h2>welcome to our site</h2>
  <p>Tusk Hollow Lodge is situated off the Kaliwa road and is home to a private game sanctuary of rolling hills, woodland and open plains. The lodge offers comfortable chalets, a restaurant serving local and international cuisine, and a bar overlooking the water hole where animals come to drink each evening. Guests can explore the sanctuary on foot or by vehicle, play a round at the Lirundu Country Club, or simply relax by the pool. Conference facilities and a garden for weddings make the lodge a fine venue for events, and our staff are always ready to help plan your stay.</p>
</section>

<footer class="site-footer">
  <div class="footer-links">
    <ul><li>Home</li><li>Rooms</li><li>Conferences</li><li>Cuisine</li><li>Facilities</li><li>Your Safari</li><li>Activities</li></ul>
    <ul><li>Rates &amp; Special Offers</li><li>Booking inquiries</li><li>Latest Developments</li><li>How To Get There</li><li>Gallery</li><li>Contact Us</li><li>Our Blog</li></ul>
  </div>
  <div class="follow"><span>follow us</span><i></i><i></i><i></i><i></i></div>
  <div class="address">Tusk Hollow Lodge, Nsonga Estate, Kaliwa Valley.<br>P.O. Box 4120, Nkhombe</div>
  <div class="copyright">Copyright © 2012 All Rights Reserved</div>
</footer>

</body>
</html>
```